LLC needs a business card design that emphasizes consulting and expert witness in upstream oil and g

I need a business card design for my company called Obena Field Advisory Group, LLC. My expertise is in oil and gas upstream operations management to optimize performance and also as an expert witness for law firms in oil and gas upstream operations litigation.
The final design should communicate knowledge and hands-on experience as well as trust. (Obena means rope or lasso. Perhaps "Obena" should be in the form of a rope.) I do not like the color green in any shade. My first preference would be some shade of blue.
Industry/Entity Type
Oil And Gas

```html
<!DOCTYPE html>
<html lang="en">
<head>
<meta charset="utf-8">
<title>Obena Field Advisory Group, LLC – Business Card</title>
<link rel="stylesheet" href="https://fonts.googleapis.com/css2?family=Open+Sans:wght@400;600&family=Oswald:wght@400&display=swap">
<style>
  :root {
    --backdrop: #3a3633;
    --card: #141414;
    --card-edge: #1d1d1d;
    --ink: #f4f4f4;
    --ink-soft: #cfcfcf;
    --divider: #2c2c2c;
  }
  * { margin: 0; padding: 0; box-sizing: border-box; }
  html, body { width: 1200px; height: 844px; overflow: hidden; }
  body {
    background: var(--backdrop);
    font-family: "Open Sans", Arial, sans-serif;
    color: var(--ink);
  }
  .canvas {
    position: relative;
    width: 1200px;
    height: 844px;
    display: flex;
    align-items: center;
    justify-content: center;
    gap: 40px;
  }
  .card {
    width: 500px;
    height: 286px;
    background: var(--card);
    border: 1px solid var(--card-edge);
    border-radius: 4px;
    position: relative;
    overflow: hidden;
  }

  /* Contact side */
  .card--contact { display: flex; }
  .contact__brand {
    width: 50%;
    display: flex;
    align-items: center;
    justify-content: center;
    padding-top: 40px;
  }
  .brand-name {
    font-family: "Open Sans", Arial, sans-serif;
    font-weight: 400;
    color: var(--ink);
    line-height: 1;
  }
  .contact__brand .brand-name { font-size: 54px; }
  .contact__divider {
    width: 1px;
    margin: 40px 0;
    background: var(--divider);
  }
  .contact__details {
    width: 50%;
    padding: 50px 0 0 26px;
  }
  .person__name { font-size: 22px; font-weight: 600; line-height: 1.1; }
  .person__role { font-size: 12px; color: var(--ink-soft); margin-bottom: 16px; }
  .contact__lines, .contact__address {
    font-size: 13px;
    line-height: 1.35;
    color: var(--ink-soft);
    list-style: none;
  }
  .contact__address { margin-top: 14px; font-style: normal; }

  /* Brand side */
  .card--brand {
    display: flex;
    flex-direction: column;
    align-items: center;
    justify-content: center;
    gap: 22px;
  }
  .card--brand .brand-name { font-size: 76px; color: var(--ink-soft); }
  .brand-tagline {
    font-family: "Oswald", "Arial Narrow", sans-serif;
    font-size: 26px;
    letter-spacing: 0.5px;
    text-transform: uppercase;
    color: var(--ink);
  }
</style>
</head>
<body>
<main class="canvas">
  <section class="card card--contact" aria-label="Business card, contact side">
    <div class="contact__brand">
      <span class="brand-name">Obena</span>
    </div>
    <div class="contact__divider"></div>
    <div class="contact__details">
      <p class="person__name">Daniel Marsh</p>
      <p class="person__role">Managing Director</p>
      <ul class="contact__lines">
        <li>T: 044-555 018 274</li>
        <li>E: info@obenacs.com</li>
        <li>W: www.obenacs.com</li>
      </ul>
      <address class="contact__address">
        4820, Harlan Ridge Road<br>
        Midland County, 790210.
      </address>
    </div>
  </section>

  <section class="card card--brand" aria-label="Business card, brand side">
    <span class="brand-name">Obena</span>
    <p class="brand-tagline">Field Advisory Group, LLC</p>
  </section>
</main>
</body>
</html>
```